Investment company needing business card

We are wanting a business card which looks sharp and easy on the eye. We are thinking of having a business card with the logo embossed on it, to really make it stand out. We will only have a small amount of information of the business card, person's name, position, email address and phone number

Contact Information for Business Card

Danielle Frost
Executive Assistant
+64 21 473 5162
danielf@harwickpartners.co.nz

Requirements
Must have
• Embossed logo
Should not have
• Not to be busy

```html
<!DOCTYPE html>
<html lang="en">
<head>
<meta charset="utf-8">
<title>Harwick Partners – Business Card</title>
<link href="https://fonts.googleapis.com/css2?family=Lato:wght@400;700;900&display=swap" rel="stylesheet">
<style>
  :root {
    --backdrop: #2a2a2b;
    --card: #1c1d1f;
    --card-edge: #26272a;
    --accent: #24b874;
    --muted: #6a6b6d;
    --text: #e9e9ea;
    --rule: #55575a;
  }
  * { margin: 0; padding: 0; box-sizing: border-box; }
  html, body {
    width: 1200px; height: 1108px; overflow: hidden;
    background: var(--backdrop);
    font-family: "Lato", sans-serif;
  }
  .stage {
    width: 1200px; height: 1108px;
    display: flex; align-items: center; justify-content: center; gap: 70px;
  }
  .card {
    width: 360px; height: 620px;
    background: var(--card);
    border: 1px solid var(--card-edge);
    border-radius: 22px;
    position: relative;
    overflow: hidden;
    box-shadow: 0 24px 50px rgba(0,0,0,.45);
  }
  /* Front */
  .card-front { display: flex; flex-direction: column; align-items: center; text-align: center; }
  .brand-mark {
    margin-top: 150px;
    display: flex; align-items: center; gap: 12px;
    font-weight: 900; font-size: 26px; letter-spacing: 1px;
    color: var(--accent);
    text-transform: uppercase;
  }
  .brand-mark .square { width: 22px; height: 22px; background: var(--muted); }
  .holder-name {
    margin-top: 150px;
    font-weight: 900; font-size: 26px; letter-spacing: .5px;
    color: var(--accent); text-transform: uppercase;
  }
  .holder-role { margin-top: 2px; font-size: 18px; color: var(--text); }
  .divider { width: 236px; height: 1px; background: var(--rule); margin: 16px 0 18px; }
  .contact { font-size: 17px; line-height: 1.35; color: var(--text); }
  /* Back */
  .pattern-field {
    position: absolute; inset: 0 0 150px 0;
    background: radial-gradient(ellipse at 60% 35%, #27282b 0%, #1f2022 55%, var(--card) 100%);
  }
  .back-brand {
    position: absolute; left: 0; right: 0; bottom: 80px;
    display: flex; align-items: center; justify-content: center; gap: 12px;
    font-weight: 900; font-size: 26px; letter-spacing: 1px;
    color: var(--accent); text-transform: uppercase;
  }
  .back-brand .square { width: 22px; height: 22px; background: var(--muted); }
</style>
</head>
<body>
<main class="stage">
  <article class="card card-front">
    <div class="brand-mark"><span class="square"></span>Harwick Partners</div>
    <h1 class="holder-name">Danielle Frost</h1>
    <p class="holder-role">Executive Assistant</p>
    <div class="divider"></div>
    <p class="contact">+64 21 473 5162<br>danielf@harwickpartners.co.nz</p>
  </article>
  <article class="card card-back">
    <div class="pattern-field" role="img" aria-label="Faint embossed tonal brand pattern"></div>
    <div class="back-brand"><span class="square"></span>Harwick Partners</div>
  </article>
</main>
</body>
</html>
```